TEBSIRK HOA Portal Site for Public

Clean up and organize current website; need website to look good and functional; this is a HOA (homeowner association management) website where homeowners can login and pay their bill, general information about a HOA, monthly newsletter page.
Competitors:
https://quillmarsh.example/
https://dorvinpalms.example/
https://www.kelbrookhomes.example/nevada
http://www.tpw-hoa.example/

Target Market(s)

homeowners

Industry/Entity Type

Real Estate

Coding

Coded - Design and coding required

Number of Pages Required

5+ page

Font styles to use
Serif

Colors
0292cd
33a6d7
e667a6
e34297

Requirements
Must have
• login to pay
• services page
• contact us
• order resale package
Nice to have
• page why an HOA would contract us

```html
<!DOCTYPE html>
<html lang="en">
<head>
<meta charset="utf-8">
<title>Tebsirk Association Management</title>
<link href="https://fonts.googleapis.com/css2?family=Open+Sans:wght@400;600;700;800&display=swap" rel="stylesheet">
<style>
:root{
  --green:#5b9e2f;
  --green-dark:#4d8a25;
  --ink:#222;
  --text:#3a3a3a;
  --grey-band:#e8e6e6;
  --card:#eceaea;
  --blue:#2b93d1;
  --dark:#121212;
  --footer:#17181a;
  --bottom:#0c0c0c;
  --white:#fff;
}
*{box-sizing:border-box;margin:0;padding:0}
html,body{width:1200px;height:4301px;overflow:hidden}
body{position:relative;font-family:"Open Sans",Arial,sans-serif;color:var(--text);background:var(--white)}
.abs{position:absolute}
a{color:inherit;text-decoration:none}

/* header */
.site-header{left:0;top:0;width:1200px;height:137px;background:#efefef}
.logo-disc{left:92px;top:-63px;width:300px;height:300px;border-radius:50%;background:#f4f4f4;z-index:3}
.logo-mark{left:226px;top:58px;width:34px;height:34px;background:var(--green);z-index:4}
.logo-name{left:100px;top:147px;width:284px;text-align:center;font-size:16px;font-weight:700;color:var(--ink);z-index:4;letter-spacing:.2px}
.call{left:720px;top:28px;display:flex;align-items:center;gap:10px}
.call-ring{width:36px;height:36px;border-radius:50%;border:2px solid var(--green);display:flex;align-items:center;justify-content:center}
.call-label{font-size:11px;font-weight:600;line-height:1.1;color:var(--ink)}
.call-label b{display:block;font-size:17px;font-weight:700}
.search{left:940px;top:30px;width:158px;height:29px;border:1px solid #bbb;background:#fff;font-size:13px;padding:5px 8px;color:#555}
.search svg{position:absolute;right:7px;top:7px}
.nav{left:527px;top:94px;display:flex;gap:0;font-size:16px;color:var(--ink)}
.nav a{position:absolute;white-space:nowrap}
.nav .active::after{content:"";position:absolute;left:0;right:0;bottom:-14px;height:3px;background:var(--green)}

/* hero */
.hero{left:0;top:137px;width:1200px;height:773px;background:linear-gradient(135deg,#cfcfcb 0%,#9aa0a4 40%,#6e7378 70%,#b9b6ad 100%)}
.hero-panel{left:204px;top:506px;width:797px;height:278px;background:rgba(50,50,50,.72);text-align:center;color:#fff}
.hero-panel h1{margin-top:46px;font-size:35px;font-weight:600;letter-spacing:.3px}
.hero-panel p{margin:12px auto 0;width:600px;font-size:17px;line-height:28px}
.btn{display:inline-flex;align-items:center;justify-content:center;background:var(--green);color:#fff;font-weight:600}
.hero-btn{left:487px;top:674px;width:231px;height:57px;font-size:16px}
.dots{left:566px;top:856px;display:flex;gap:8px;align-items:center}
.dots span{width:14px;height:14px;border-radius:50%;background:#fff}
.dots span:first-child{width:22px;height:22px;border:3px solid #fff;background:transparent;position:relative}
.dots span:first-child::after{content:"";position:absolute;inset:3px;border-radius:50%;background:#fff}
.hero-curve{left:0;top:810px}

/* section titles */
.title{font-size:31px;font-weight:600;color:var(--ink);display:flex;align-items:center;gap:16px;letter-spacing:.3px}
.title::after{content:"";width:88px;height:3px;background:var(--green)}
.title.light{color:#fff}

/* welcome */
.welcome-title{left:98px;top:1012px}
.welcome-copy{left:98px;top:1085px;width:453px;font-size:14.5px;line-height:25.8px;text-align:justify}
.read-more{font-size:15px;gap:6px;height:38px;padding:0 15px}
.read-more i{width:13px;height:13px;border:1.5px solid #fff;border-radius:50%;display:inline-block}
.welcome-btn{left:98px;top:1417px;width:147px}
.blue-block{left:656px;top:1015px;width:444px;height:437px;background:var(--blue)}
.family-photo{left:601px;top:1045px;width:472px;height:425px;background:linear-gradient(160deg,#5a6b84 0%,#8592a5 45%,#6f8c4a 85%,#5d7d36 100%)}

/* services */
.services-band{left:0;top:1574px;width:1200px;height:516px;background:var(--grey-band)}
.svc-icon{width:116px;height:116px}
.svc-label{width:220px;text-align:center;font-size:15px;font-weight:600;color:var(--ink)}
.services-title{left:639px;top:1651px}
.services-copy{left:641px;top:1708px;width:441px;font-size:14.5px;line-height:28.3px;text-align:justify}
.services-btn{left:643px;top:1981px;width:143px}

/* team */
.team-title{left:464px;top:2182px}
.team-card{width:326px;height:371px;background:var(--card);text-align:center}
.team-card.featured{height:443px;box-shadow:0 3px 10px rgba(0,0,0,.25)}
.team-photo{width:100%;height:237px}
.team-card h3{margin-top:16px;font-size:15px;font-weight:700;color:var(--ink)}
.team-card p{margin:10px auto 0;width:300px;font-size:14.5px;line-height:19px;color:#444}
.team-social{margin-top:8px;display:flex;justify-content:center;gap:8px}
.team-social span{width:11px;height:11px;border-radius:50%;background:#222}
.team-btn{margin-top:12px;width:160px;height:40px;font-size:15px;gap:6px;font-weight:700}
.team-btn i{width:13px;height:13px;border:1.5px solid #fff;border-radius:50%}

/* blog */
.blog-band{left:0;top:2817px;width:1200px;height:825px;background:linear-gradient(180deg,#1a1a1a,#0b0b0b)}
.blog-title{left:456px;top:2876px}
.blog-main-img{left:98px;top:2966px;width:595px;height:339px;background:linear-gradient(150deg,#9fb0c4 0%,#5e6f86 40%,#3a475a 70%,#6b8a47 100%)}
.author{left:98px;top:3318px;width:595px;height:46px;border-bottom:1px solid #3a3a3a;display:flex;align-items:center;color:#fff}
.avatar{width:46px;height:46px;border-radius:50%;background:#cfcfcf}
.author-name{margin-left:22px;font-size:20px;letter-spacing:.5px}
.author-date{margin-left:auto;font-size:15px;color:#ddd}
.blog-head{left:100px;top:3386px;font-size:21px;font-weight:600;color:#fff}
.blog-text{left:100px;top:3424px;width:580px;font-size:14.5px;line-height:25.6px;color:#ddd;text-align:justify}
.blog-card{width:374px;background:#fff}
.blog-card .img{height:222px}
.blog-card span{display:block;height:53px;line-height:53px;padding-left:24px;font-size:15px;color:#333}

/* cta */
.cta-band{left:0;top:3642px;width:1200px;height:290px;background:#e6e4e4;text-align:center}
.cta-band h2{margin-top:62px;font-size:24px;font-weight:800;color:#1b1b1b;letter-spacing:.3px}
.cta-band p{margin:12px auto 0;width:800px;font-size:15px;line-height:26px;color:#333}
.cta-btn{left:521px;top:3812px;width:157px;height:49px;font-size:17px}

/* footer */
.site-footer{left:0;top:3932px;width:1200px;height:316px;background:var(--footer);color:#fff}
.foot-h{font-size:20px;font-weight:700;letter-spacing:.3px}
.foot-link{font-size:17px;color:#e8e8e8}
.foot-contact{font-size:15px;color:#e8e8e8;display:flex;gap:10px;line-height:20px}
.newsletter{left:729px;top:4061px;width:371px;height:38px;display:flex}
.newsletter .field{flex:1;background:#fff;font-size:13px;color:#444;padding:10px 12px}
.newsletter .sub{width:132px;background:var(--green);color:#fff;font-size:15px;font-weight:700;display:flex;align-items:center;justify-content:center}
.foot-circle{width:27px;height:27px;border-radius:50%;border:2px solid #fff}
.bottom-bar{left:0;top:4248px;width:1200px;height:53px;background:var(--bottom);color:#ddd;text-align:center;line-height:53px;font-size:15px}
</style>
</head>
<body>

<header class="abs site-header">
  <div class="abs call">
    <div class="call-ring">
      <svg width="18" height="18" viewBox="0 0 24 24" fill="none" stroke="#5b9e2f" stroke-width="2"><path d="M5 3h4l2 5-3 2a12 12 0 0 0 6 6l2-3 5 2v4a2 2 0 0 1-2 2A17 17 0 0 1 3 5a2 2 0 0 1 2-2z"/></svg>
    </div>
    <div class="call-label">CALL NOW<b>(555) 014-2278</b></div>
  </div>
  <div class="abs search">Search
    <svg width="14" height="14" viewBox="0 0 24 24" fill="none" stroke="#222" stroke-width="3"><circle cx="10" cy="10" r="7"/><path d="M15 15l6 6"/></svg>
  </div>
  <nav class="abs nav">
    <a class="active" style="left:0">HOME</a>
    <a style="left:82px">ABOUT</a>
    <a style="left:171px">SERVICES</a>
    <a style="left:281px">PARTNER WITH US</a>
    <a style="left:463px">CONTCAT US</a>
  </nav>
</header>
<div class="abs logo-disc"></div>
<div class="abs logo-mark"></div>
<div class="abs logo-name">TEBSIRK ASSOCIATION MANAGEMENT</div>

<section>
  <div class="abs hero" role="img" aria-label="Smiling couple holding house keys in front of a modern white home"></div>
  <svg class="abs hero-curve" width="1200" height="110" viewBox="0 0 1200 110">
    <path d="M0 20 Q600 150 1200 20 L1200 110 L0 110 Z" fill="#fff"/>
    <path d="M0 20 Q600 150 1200 20" fill="none" stroke="#5b9e2f" stroke-width="4"/>
  </svg>
  <div class="abs hero-panel">
    <h1>LETS TEAM UP FOR YOUR &nbsp;COMMUNITY</h1>
    <p>we think your community and our team make a great fit wed love to hear from you!</p>
  </div>
  <a class="abs btn hero-btn">LOGIN TO PAY</a>
  <div class="abs dots"><span></span><span></span><span></span></div>
</section>

<section>
  <h2 class="abs title welcome-title">WELCOME TO TEBSIRK</h2>
  <p class="abs welcome-copy">As the leading residential property management company in North America, we work hard to help your community thrive. Our dedication, responsiveness and integrity are why thousands of communities across the U.S. and Canada choose Kelbrook Residential to manage their properties. Kelbrook Residential works with all types of properties:<br>We also have special expertise working with complex communities that have large budgets and offer numerous amenities to their residents. In addition, we manage commercial associations and mixed-use developments, as well as multi-family and investor-owned rental and REO properties for institutional and private equity clients.</p>
  <a class="abs btn read-more welcome-btn">Read More <i></i></a>
  <div class="abs blue-block"></div>
  <div class="abs family-photo" role="img" aria-label="Family of five standing on the lawn in front of their home"></div>
</section>

<section>
  <div class="abs services-band"></div>
  <svg class="abs svc-icon" style="left:141px;top:1651px" viewBox="0 0 116 116" fill="none" stroke="#5b9e2f" stroke-width="3"><path d="M58 4 112 58 58 112 4 58Z"/><path d="M64 6 114 56" stroke-width="5"/><circle cx="58" cy="58" r="18"/><path d="M58 47v11l7 5"/></svg>
  <svg class="abs svc-icon" style="left:398px;top:1651px" viewBox="0 0 116 116" fill="none" stroke="#5b9e2f" stroke-width="3"><path d="M58 4 112 58 58 112 4 58Z"/><path d="M64 6 114 56" stroke-width="5"/><circle cx="58" cy="58" r="16"/><circle cx="58" cy="58" r="6"/></svg>
  <svg class="abs svc-icon" style="left:141px;top:1840px" viewBox="0 0 116 116" fill="none" stroke="#5b9e2f" stroke-width="3"><path d="M58 4 112 58 58 112 4 58Z"/><path d="M64 6 114 56" stroke-width="5"/><circle cx="46" cy="48" r="5"/><circle cx="58" cy="46" r="5"/><circle cx="70" cy="48" r="5"/><path d="M40 72V58h36v14"/></svg>
  <svg class="abs svc-icon" style="left:398px;top:1840px" viewBox="0 0 116 116" fill="none" stroke="#5b9e2f" stroke-width="3"><path d="M58 4 112 58 58 112 4 58Z"/><path d="M64 6 114 56" stroke-width="5"/><path d="M40 56 58 42 76 56V74H40Z"/><path d="M52 74V62h12v12"/></svg>
  <div class="abs svc-label" style="left:100px;top:1784px">24/7 Emergency Response</div>
  <div class="abs svc-label" style="left:342px;top:1784px">Maintenance Request</div>
  <div class="abs svc-label" style="left:102px;top:1972px">Community Management</div>
  <div class="abs svc-label" style="left:346px;top:1972px">Property Mangement</div>
  <h2 class="abs title services-title">SERVICES</h2>
  <p class="abs services-copy">Accessible, licensed Association Managers24 hour Web site access: online account information24 hour emergency serviceProvide monthly financial reports to the Board of DirectorsRead, study and understand all governing documents of the Association. Correspond with members in violation of the CC&amp;Rs, By-laws, Rules &amp; Regulations and report the status of all noncompliance to the Board of Directors in a timely manner Act as the custodian of the corporate records. Coordinate preparing annual tax returns for the Association.</p>
  <a class="abs btn read-more services-btn">Read More <i></i></a>
</section>

<section>
  <h2 class="abs title team-title">OUR TEAM</h2>
  <div class="abs team-card" style="left:98px;top:2273px">
    <div class="team-photo" role="img" aria-label="Portrait of a team member in a dark shirt" style="background:linear-gradient(135deg,#3f6178,#27384a)"></div>
    <h3>OWEN HALVARD</h3>
    <p>Sed ut perspiciatis unde omnis iste natus error sit voluptatem accusantium doloremque laperiam</p>
  </div>
  <div class="abs team-card featured" style="left:439px;top:2273px">
    <div class="team-photo" role="img" aria-label="Portrait of a team member in a light blue shirt" style="background:linear-gradient(135deg,#dfe6ee,#9db7cf)"></div>
    <h3>REID CASTELLAN</h3>
    <p>Sed ut perspiciatis unde omnis iste natus error sit voluptatem accusantium doloremque aperiam</p>
    <div class="team-social"><span></span><span></span><span></span></div>
    <a class="btn team-btn">Read More <i></i></a>
  </div>
  <div class="abs team-card" style="left:776px;top:2273px">
    <div class="team-photo" role="img" aria-label="Portrait of a team member in a suit" style="background:linear-gradient(135deg,#d9d6d1,#3c3a38)"></div>
    <h3>LIAM BROCKETT</h3>
    <p>Sed ut perspiciatis unde omnis iste natus error sit voluptatem accusantium doloremque aperiam</p>
  </div>
</section>

<section>
  <div class="abs blog-band"></div>
  <h2 class="abs title light blog-title">LATEST BLOG</h2>
  <div class="abs blog-main-img" role="img" aria-label="Family greeting a woman outside a blue-sided house"></div>
  <div class="abs author">
    <div class="avatar" role="img" aria-label="Author portrait"></div>
    <span class="author-name">CORWIN</span>
    <span class="author-date">November 11, 2019</span>
  </div>
  <h3 class="abs blog-head">Lorem Ipsum</h3>
  <p class="abs blog-text">Sed ut perspiciatis unde omnis iste natus error sit voluptatem accusantium doloremque laudantium, totam rem aperiam, eaque ipsa quae ab illo inventore veritatis et quasi architecto beatae vitae dicta sunt explicabo. Nemo enim ipsam voluptatem quia voluptas sit aspernatur aut odit aut fugit, sed quia consequuntur magni dolores eos qui ratione voluptatem sequi nesciunt. Neque porro quisquam</p>
  <div class="abs blog-card" style="left:728px;top:2971px">
    <div class="img" role="img" aria-label="Two women laughing together on a sofa with mugs" style="background:linear-gradient(135deg,#e9e7e4,#b9b3ab)"></div>
    <span>Lorem Ipsum</span>
  </div>
  <div class="abs blog-card" style="left:728px;top:3295px">
    <div class="img" role="img" aria-label="Couple carrying moving boxes into a new home" style="background:linear-gradient(135deg,#f1efec,#a9a49c)"></div>
    <span>Lorem Ipsum</span>
  </div>
</section>

<section class="abs cta-band">
  <h2>YOUR BEST CHOICE FOR HOA MANAGEMENT IN THE LAS VEGAS VALLEY</h2>
  <p>Tebsirk Association Management is always striving to be of service to the city and community we live and work in. Our team is dedicated into protecting and serving our owners and members.</p>
</section>
<a class="abs btn cta-btn">PAY DUES</a>

<footer class="abs site-footer"></footer>
<div class="abs foot-h" style="left:118px;top:4010px;color:#fff">QUICK LINKS</div>
<a class="abs foot-link" style="left:121px;top:4050px">Home</a>
<a class="abs foot-link" style="left:121px;top:4086px">About</a>
<a class="abs foot-link" style="left:121px;top:4121px">Services</a>
<a class="abs foot-link" style="left:121px;top:4158px">Partner With Us</a>
<a class="abs foot-link" style="left:121px;top:4193px">contcat us</a>

<div class="abs foot-h" style="left:416px;top:4010px;color:#fff">CONTACT US</div>
<div class="abs foot-contact" style="left:416px;top:4057px">
  <svg width="12" height="16" viewBox="0 0 12 16"><path d="M6 0a6 6 0 0 1 6 6c0 4-6 10-6 10S0 10 0 6a6 6 0 0 1 6-6z" fill="#fff"/><circle cx="6" cy="6" r="2" fill="#17181a"/></svg>
  <span>4120 Harlow Ridge Ave Henderson,<br>NV 89000</span>
</div>
<div class="abs foot-contact" style="left:414px;top:4113px">
  <svg width="15" height="15" viewBox="0 0 24 24" fill="none" stroke="#fff" stroke-width="2"><path d="M5 3h4l2 5-3 2a12 12 0 0 0 6 6l2-3 5 2v4a2 2 0 0 1-2 2A17 17 0 0 1 3 5a2 2 0 0 1 2-2z"/></svg>
  <span>(555) 014-2278</span>
</div>
<div class="abs foot-contact" style="left:414px;top:4149px">
  <svg width="16" height="14" viewBox="0 0 16 12" fill="none" stroke="#fff" stroke-width="1.3"><rect x="1" y="1" width="14" height="10"/><path d="M1 1l7 6 7-6"/></svg>
  <span>hello@tebsirk.example</span>
</div>

<div class="abs foot-h" style="left:729px;top:4010px;color:#fff">NEWSLETTER</div>
<div class="abs newsletter"><div class="field">Enter your email</div><div class="sub">SUBSCRIBE</div></div>
<div class="abs foot-circle" style="left:731px;top:4124px"></div>
<div class="abs foot-circle" style="left:766px;top:4124px"></div>
<div class="abs foot-circle" style="left:801px;top:4124px"></div>
<div class="abs foot-circle" style="left:836px;top:4124px"></div>

<div class="abs bottom-bar">Copyrights © 2019 All Rights Reserved</div>

</body>
</html>
```